Brightbay Orthodontics business card design

Need a business card design that reflects our re-branding (orthodontic office - braces) and a new partnership with a pediatric dental office. We would like to include "for adults and children" on the card as well so adults know they are welcome to get their braces here as well. Office design is modern and would like business card to reflect a modern type look. Here's the text we would like to be included on the card:

Darren Wolcott, DDS, MSD
5214 West Linden Avenue, Suite 204
Mansfield, TX 76991
555-418-2637
www.brightbayortho.example
info@brightbayortho.example

Can we add the following to the existing designs? Darren Wolcott, DDS, MSD 5214 West Linden Avenue, Suite 204 Mansfield, TX 76991 555-418-2637

Does anyone have any more vertical designs available? Thanks!

Dental

```html
<!DOCTYPE html>
<html lang="en">
<head>
<meta charset="utf-8">
<title>Brightbay Orthodontics business card</title>
<link rel="stylesheet" href="https://fonts.googleapis.com/css2?family=Open+Sans:wght@400;600;700&display=swap">
<style>
  :root {
    --bg: #d9d7d2;
    --card: #ffffff;
    --card-shade: #e6e6e6;
    --ink: #222222;
    --ink-soft: #444444;
    --ink-muted: #777777;
    --name-blue: #1b75bc;
    --icon-green: #3aa935;
    --band-yellow: #fff200;
    --band-blue: #1b75bc;
    --band-magenta: #e0137f;
    --band-green: #5aa02c;
    --band-orange: #d2761a;
  }
  * { box-sizing: border-box; margin: 0; padding: 0; }
  html, body { width: 1200px; height: 871px; overflow: hidden; }
  body {
    background: var(--bg);
    font-family: "Open Sans", Arial, sans-serif;
    color: var(--ink);
    position: relative;
  }
  .card {
    position: absolute;
    width: 560px;
    height: 320px;
    background: linear-gradient(135deg, var(--card) 40%, var(--card-shade) 100%);
    box-shadow: 0 10px 28px rgba(0,0,0,0.28);
    overflow: hidden;
  }
  .card--front { left: 70px; top: 110px; }
  .card--back { left: 570px; top: 440px; background: var(--card); }

  .brand {
    display: flex;
    align-items: center;
    gap: 14px;
  }
  .brand__dot {
    width: 44px; height: 44px;
    border-radius: 50%;
    background: var(--band-blue);
    flex: none;
  }
  .brand__name {
    display: block;
    font-weight: 700;
    color: var(--ink);
    line-height: 1.05;
  }
  .brand__tagline {
    display: block;
    margin-top: 6px;
    font-size: 12px;
    font-weight: 400;
    color: var(--ink-muted);
  }
  .card--front .brand {
    position: absolute;
    left: 0; right: 0; top: 0; bottom: 0;
    justify-content: center;
  }
  .card--front .brand__name { font-size: 38px; }
  .card--front .brand__tagline { font-size: 15px; margin-top: 8px; }

  .card--back .brand {
    position: absolute;
    right: 30px; top: 74px;
  }
  .card--back .brand__dot { width: 30px; height: 30px; }
  .card--back .brand__name { font-size: 24px; }

  .contact {
    position: absolute;
    left: 36px; top: 62px;
    font-size: 13px;
    color: var(--ink-soft);
  }
  .contact__name {
    color: var(--name-blue);
    font-weight: 700;
    font-size: 18px;
  }
  .contact__role {
    font-size: 11px;
    color: var(--ink-muted);
    margin-bottom: 14px;
  }
  .contact__address { line-height: 1.45; margin-bottom: 12px; }
  .contact__list { list-style: none; }
  .contact__item {
    display: flex;
    align-items: center;
    gap: 12px;
    line-height: 1.75;
  }
  .contact__icon { width: 12px; height: 12px; flex: none; }

  .band {
    position: absolute;
    left: 0; right: 0; bottom: 0;
    height: 16px;
    display: flex;
  }
  .band span { flex: 1; }
  .band .y { background: var(--band-yellow); }
  .band .b { background: var(--band-blue); }
  .band .m { background: var(--band-magenta); }
  .band .g { background: var(--band-green); }
  .band .o { background: var(--band-orange); }
</style>
</head>
<body>

  <section class="card card--front" aria-label="Card front">
    <div class="brand">
      <span class="brand__dot"></span>
      <div class="brand__text">
        <span class="brand__name">Brightbay Orthodontics</span>
        <span class="brand__tagline">for adults and children</span>
      </div>
    </div>
  </section>

  <section class="card card--back" aria-label="Card back">
    <div class="contact">
      <p class="contact__name">Darren Wolcott</p>
      <p class="contact__role">DDS, MSD</p>
      <p class="contact__address">5214 West Linden Avenue, Suite 204<br>Mansfield, TX 76991</p>
      <ul class="contact__list">
        <li class="contact__item">
          <svg class="contact__icon" viewBox="0 0 12 12" aria-hidden="true">
            <path d="M2.5 1 L4.5 1 L5.2 3.6 L4 4.6 Q5 7 7.4 8 L8.4 6.8 L11 7.5 L11 9.5 Q11 11 9.5 11 Q1 10 1 2.5 Q1 1 2.5 1 Z" fill="none" stroke="var(--icon-green)" stroke-width="1"/>
          </svg>
          <span>555-418-2637</span>
        </li>
        <li class="contact__item">
          <svg class="contact__icon" viewBox="0 0 12 12" aria-hidden="true">
            <rect x="0.5" y="2.5" width="11" height="7" fill="none" stroke="var(--icon-green)" stroke-width="1"/>
            <path d="M0.5 2.5 L6 7 L11.5 2.5" fill="none" stroke="var(--icon-green)" stroke-width="1"/>
          </svg>
          <span>info@brightbayortho.example</span>
        </li>
        <li class="contact__item">
          <svg class="contact__icon" viewBox="0 0 12 12" aria-hidden="true">
            <circle cx="6" cy="6" r="5.3" fill="none" stroke="var(--icon-green)" stroke-width="1"/>
            <ellipse cx="6" cy="6" rx="2.3" ry="5.3" fill="none" stroke="var(--icon-green)" stroke-width="1"/>
            <line x1="0.7" y1="6" x2="11.3" y2="6" stroke="var(--icon-green)" stroke-width="1"/>
          </svg>
          <span>www.brightbayortho.example</span>
        </li>
      </ul>
    </div>

    <div class="brand">
      <span class="brand__dot"></span>
      <div class="brand__text">
        <span class="brand__name">Brightbay<br>Orthodontics</span>
        <span class="brand__tagline">for adults and children</span>
      </div>
    </div>

    <div class="band" aria-hidden="true">
      <span class="y"></span><span class="b"></span><span class="m"></span><span class="g"></span><span class="o"></span>
    </div>
  </section>

</body>
</html>
```